Personal Web page for recruiter and owner of consulting firm

I work full time as a recruiter so I want a page that allows for me to support my efforts. I would like a long single page, I need to be able to upload four two minute videos, and 4 images. I also want the color scheme to match with my consulting company. I own the domain marcusfenwold.net already through wordpress . I took a shot at it myself and its terrible.

Target Market(s)

Potential clients

Industry/Entity Type

Management Consulting

Logo Text

marcus fenwold

Font styles to use
Serif

Requirements
Must have
• Must in color scheme go well with my consulting company logo attached
• Must be able to upload 4 two minute videos and 4 images (photos of me)
• Single long scroll page
• Modern and clean
Nice to have
• Easy for me to update videos images and text without complex coding
Should not have
• I want the design and feel to go well with my logos not exactly replicate it

```html
<!DOCTYPE html>
<html lang="en">
<head>
<meta charset="utf-8">
<title>marcus fenwold</title>
<link href="https://fonts.googleapis.com/css2?family=Lora:wght@400;500;600&family=Open+Sans:wght@400;600;700&display=swap" rel="stylesheet">
<style>
:root{
  --navy:#0c2a4f;
  --navy-deep:#09203d;
  --sky:#6cb0e4;
  --ink:#222;
  --muted:#555;
  --soft:#f3f3f3;
  --line:#dcdcdc;
  --white:#fff;
}
*{box-sizing:border-box;margin:0;padding:0}
html,body{width:1200px;height:3830px;overflow:hidden}
body{position:relative;background:var(--white);font-family:"Open Sans",Arial,sans-serif;color:var(--ink)}
.display{font-family:"Lora",Georgia,serif}
.body-copy{font-size:12px;line-height:20px;color:var(--muted)}

/* header */
.site-header{position:absolute;left:0;top:0;width:1200px;height:85px;background:var(--white)}
.brand{position:absolute;left:97px;top:24px;font-family:"Lora",Georgia,serif;font-size:30px;font-weight:400;line-height:36px;color:var(--navy);white-space:nowrap}
.nav{position:absolute;right:97px;top:32px;display:flex;gap:44px;font-size:13px;font-weight:400;color:var(--ink);align-items:center}
.nav .sep{width:1px;height:16px;background:var(--ink);margin-left:-18px}

/* hero */
.hero{position:absolute;left:0;top:85px;width:1200px;height:477px;overflow:hidden}
.hero-photo{position:absolute;inset:0;background:linear-gradient(90deg,#6f8598 0%,#c9ccd0 45%,#8c8a8b 75%,#4c4a4c 100%)}
.hero-panel{position:absolute;inset:0}
.hero .welcome{position:absolute;left:152px;top:135px;color:var(--white);font-size:27px;font-weight:400}
.hero .title{position:absolute;left:150px;top:170px;color:var(--white);font-size:60px;font-weight:600;line-height:72px}
.hero .lede{position:absolute;left:152px;top:260px;width:380px;color:var(--white);font-size:14px;line-height:25px}
.hero .arrows{position:absolute;left:540px;top:340px;display:flex;gap:6px}
.hero .arrows span{width:27px;height:27px;border-radius:50%;background:rgba(255,255,255,.45);display:flex;align-items:center;justify-content:center}

/* icon bar */
.icon-bar{position:absolute;left:0;top:562px;width:1200px;height:107px;background:var(--soft);display:flex;justify-content:center}
.icon-bar .item{width:168px;text-align:center;padding-top:22px;font-size:15px;letter-spacing:1px;color:var(--ink)}
.icon-bar svg{display:block;margin:0 auto 8px}

/* about */
.about h2{position:absolute;left:97px;top:734px;font-size:31px;font-weight:500;letter-spacing:2px}
.about .intro{position:absolute;left:97px;top:788px;width:512px;font-size:15px;line-height:28px;color:#333;text-align:justify}
.about .detail{position:absolute;left:97px;top:897px;width:512px;text-align:justify}
.btn{position:absolute;display:flex;align-items:center;justify-content:center;font-size:13px;font-weight:600;letter-spacing:.5px}
.btn-navy{background:var(--navy);color:var(--white)}
.btn-outline{border:2px solid var(--navy);color:var(--navy);background:var(--white)}
.years{position:absolute;left:700px;top:730px;width:357px;height:355px;background:linear-gradient(135deg,#1e2f3e,#3c4a57)}
.years .inner{position:absolute;left:42px;top:30px;width:288px;height:295px;background:#d8d9da;border:6px solid rgba(255,255,255,.5)}
.years .num{position:absolute;left:18px;top:40px;font-size:110px;line-height:110px;color:#222;font-weight:400}
.years .label{position:absolute;left:18px;top:155px;font-size:36px;line-height:48px;color:#222;font-weight:400}
.divider{position:absolute;left:97px;top:1144px;width:1006px;height:1px;background:var(--line)}

/* featured */
.section-title{position:absolute;left:0;width:1200px;text-align:center;font-size:29px;letter-spacing:2px;font-weight:500}
.photo{position:absolute}
.card{position:absolute;background:var(--white);border:3px solid #e5e5e5;box-shadow:0 2px 10px rgba(0,0,0,.12);padding:22px 26px}
.card .kicker{font-size:13px;font-weight:700;color:#333;margin-bottom:12px}
.card h3{font-size:20px;line-height:34px;font-weight:600;color:#333;margin-bottom:14px}
.card p{font-size:11.5px;line-height:21px;color:var(--muted)}

/* video */
.video-band{position:absolute;left:0;top:2017px;width:1200px;height:388px;background:linear-gradient(90deg,#3a3838 0%,#6c6a69 35%,#5a5858 65%,#2f2d2d 100%)}
.video-band .play{position:absolute;left:573px;top:83px}
.video-band h2{position:absolute;left:0;top:160px;width:1200px;text-align:center;color:var(--white);font-size:30px;letter-spacing:2px;font-weight:500}
.video-band p{position:absolute;left:0;top:207px;width:1200px;text-align:center;color:#eee;font-size:13px}

/* services */
.service{position:absolute;width:270px;text-align:center;top:2555px}
.service .ring{width:124px;height:124px;margin:0 auto;border-radius:50%;border:1px solid #ddd;display:flex;align-items:center;justify-content:center;background:var(--white)}
.service .ring span{width:104px;height:104px;border-radius:50%;border:1px solid #e3e3e3;display:flex;align-items:center;justify-content:center}
.service h4{margin-top:18px;font-size:18px;font-weight:400;color:#222}
.service p{margin-top:6px;font-size:12px;line-height:24px;color:#444}

/* news */
.news-band{position:absolute;left:0;top:2936px;width:1200px;height:480px;background:linear-gradient(90deg,#f4f4f4,#eef2f5)}
.callback{position:absolute;left:97px;top:3010px;width:317px;height:327px;background:var(--navy);padding:22px 38px;color:var(--white)}
.callback h3{font-size:16px;letter-spacing:2px;font-weight:600}
.callback p{font-size:12px;line-height:22px;margin-top:10px;color:#dfe6ee}
.callback .field{height:31px;background:#1c4373;margin-top:12px;padding:0 12px;font-size:11px;line-height:31px;color:#9fb3c9}
.callback .submit{height:34px;background:var(--sky);margin-top:12px;text-align:center;line-height:34px;font-size:14px;font-weight:700}
.news-title{position:absolute;left:462px;top:3003px;font-size:28px;letter-spacing:2px;font-weight:500}
.news-card{position:absolute;top:3064px;width:297px}
.news-card .pic{height:153px}
.news-card h4{margin-top:24px;font-size:16px;font-weight:700;color:#222}
.news-card p{margin-top:8px;font-size:12px;line-height:20px;color:#444}
.news-card a{display:block;margin-top:12px;font-size:13px;font-weight:700;color:var(--navy);text-decoration:none}

/* footer */
.footer .about-text{position:absolute;left:97px;top:3538px;width:320px;font-size:12px;line-height:22px;color:#444}
.contact{position:absolute;top:3455px;display:flex;align-items:center;gap:18px;font-size:11.5px;color:#444;line-height:17px}
.contact .dot{width:40px;height:40px;border-radius:50%;background:#222;display:flex;align-items:center;justify-content:center;flex:none}
.footer .rule{position:absolute;left:462px;top:3530px;width:641px;height:1px;background:var(--line)}
.col{position:absolute;top:3566px}
.col h5{font-size:14px;font-weight:700;letter-spacing:1px;color:#222;margin-bottom:12px}
.col li{list-style:none;font-size:12px;line-height:28px;color:#444}
.socials{position:absolute;left:97px;top:3664px;display:flex;gap:10px}
.socials span{width:35px;height:35px;border-radius:50%;background:#222}
.newsletter .input{width:244px;height:34px;border:1px solid #ddd;background:var(--white);margin-top:8px;font-size:11px;line-height:32px;padding-left:12px;color:#777}
.newsletter .go{width:244px;height:34px;background:var(--navy);color:var(--white);margin-top:4px;text-align:center;line-height:34px;font-size:14px;font-weight:700}
.copyright{position:absolute;left:0;top:3779px;width:1200px;height:51px;border-top:1px solid var(--line);text-align:center;line-height:50px;font-size:11px;color:#555}
</style>
</head>
<body>

<header class="site-header">
  <div class="brand">marcus fenwold</div>
  <nav class="nav">
    <span>HOME</span><span>ABOUT</span><span>SERVICES</span><span>PROJECTS</span><span>NEWS</span><span>CONTACT</span><span class="sep"></span>
    <svg width="14" height="14" viewBox="0 0 14 14"><circle cx="5.5" cy="5.5" r="4" fill="none" stroke="#222" stroke-width="2"/><line x1="8.5" y1="8.5" x2="13" y2="13" stroke="#222" stroke-width="2"/></svg>
  </nav>
</header>

<section class="hero">
  <div class="hero-photo" role="img" aria-label="Photo of a businesswoman smiling at her phone in an office"></div>
  <svg class="hero-panel" width="1200" height="477" viewBox="0 0 1200 477">
    <defs><linearGradient id="heroBlue" x1="0" y1="0" x2="1" y2="0"><stop offset="0" stop-color="#0c2a4f" stop-opacity=".95"/><stop offset="1" stop-color="#1b4a7a" stop-opacity=".85"/></linearGradient></defs>
    <polygon points="0,0 460,0 705,477 0,477" fill="url(#heroBlue)"/>
    <polygon points="460,0 520,0 760,477 705,477" fill="#ffffff" fill-opacity=".18"/>
  </svg>
  <div class="welcome display">WELCOME TO</div>
  <div class="title display">FENWOLD.</div>
  <p class="lede">Lorem ipsum dolor sit amet consectetur adipisicing elit sed do eiusmod temp incidunt ut labore et dolore magna</p>
  <div class="arrows">
    <span><svg width="10" height="10" viewBox="0 0 10 10"><polyline points="7,1 3,5 7,9" fill="none" stroke="#fff" stroke-width="2"/></svg></span>
    <span><svg width="10" height="10" viewBox="0 0 10 10"><polyline points="3,1 7,5 3,9" fill="none" stroke="#fff" stroke-width="2"/></svg></span>
  </div>
</section>

<section class="icon-bar">
  <div class="item"><svg width="34" height="30" viewBox="0 0 34 30"><polygon points="17,1 33,8 1,8" fill="#222"/><rect x="4" y="10" width="4" height="14" fill="#222"/><rect x="12" y="10" width="4" height="14" fill="#222"/><rect x="19" y="10" width="4" height="14" fill="#222"/><rect x="26" y="10" width="4" height="14" fill="#222"/><rect x="1" y="25" width="32" height="4" fill="#222"/></svg>CONSULTING</div>
  <div class="item"><svg width="34" height="30" viewBox="0 0 34 30"><polyline points="2,2 2,28 33,28" fill="none" stroke="#222" stroke-width="2"/><polyline points="5,22 13,13 19,18 31,5" fill="none" stroke="#222" stroke-width="2.5"/></svg>EXPERTISE</div>
  <div class="item"><svg width="34" height="30" viewBox="0 0 34 30"><polyline points="2,2 2,28 33,28" fill="none" stroke="#222" stroke-width="2"/><rect x="7" y="14" width="4" height="12" fill="#222"/><rect x="14" y="8" width="4" height="18" fill="#222"/><rect x="21" y="11" width="4" height="15" fill="#222"/><rect x="28" y="5" width="4" height="21" fill="#222"/></svg>HIRE</div>
  <div class="item"><svg width="34" height="30" viewBox="0 0 34 30"><ellipse cx="17" cy="13" rx="15" ry="10" fill="none" stroke="#222" stroke-width="2.5"/><polygon points="8,20 6,28 15,22" fill="#222"/></svg>REVIEWS</div>
  <div class="item"><svg width="34" height="30" viewBox="0 0 34 30"><polygon points="4,11 12,11 26,3 26,25 12,17 4,17" fill="#222"/><rect x="9" y="17" width="4" height="9" fill="#222"/><line x1="29" y1="11" x2="33" y2="9" stroke="#222" stroke-width="2"/><line x1="29" y1="17" x2="33" y2="19" stroke="#222" stroke-width="2"/></svg>FEEDBACK</div>
  <div class="item"><svg width="34" height="30" viewBox="0 0 34 30"><rect x="3" y="12" width="6" height="16" fill="none" stroke="#222" stroke-width="2"/><path d="M11 13 L17 2 Q20 2 20 6 L19 11 L29 11 Q32 12 31 15 L28 26 Q27 28 24 28 L11 28 Z" fill="none" stroke="#222" stroke-width="2"/></svg>SUCCESS</div>
</section>

<section class="about">
  <h2 class="display">A CONSULTING FIRM</h2>
  <p class="intro">Contrary to popular belief, Lorem Ipsum is not simply random text. It has roots in a piece of classical Latin literature from 45 BC, making it over 2000 years old.</p>
  <p class="detail body-copy">There are many variations of passages of Lorem Ipsum available, but the majority have suffered alteration in some form, by injected humour, or randomised words which don't look even slightly believable. If you are going to use a passage of Lorem Ipsum, you need to be sure there isn't anything embarrassing the majority have suffered</p>
  <div class="btn btn-navy" style="left:97px;top:1030px;width:128px;height:41px">READ MORE</div>
  <div class="years">
    <div class="inner">
      <div class="num display">25</div>
      <div class="label display">YEARS OF<br>EXPERIENCE</div>
    </div>
  </div>
  <div class="divider"></div>
</section>

<section class="featured">
  <h2 class="section-title display" style="top:1212px">FEATURED PROJECT</h2>
  <div class="photo" style="left:97px;top:1284px;width:508px;height:345px;background:linear-gradient(135deg,#d9d3c8,#efe9df 50%,#b9b0a4)" role="img" aria-label="Photo of a team meeting around a table, seen from above"></div>
  <div class="card" style="left:605px;top:1300px;width:493px;height:262px">
    <div class="kicker">Vellum Layout</div>
    <h3>Many desktop publishing packages web page editors now use Lorem Ipsum</h3>
    <p>It is a long established fact that a reader will be distracted by the readable content of a page when looking at its layout. The point of using Lorem Ipsum is that it has a more-or-less normal distribution of letters, as opposed to using 'Content here, content here', making it look like readable English.</p>
  </div>
  <div class="photo" style="left:592px;top:1596px;width:508px;height:344px;background:linear-gradient(120deg,#5a6a78,#c9b7a8 55%,#e9d6e4)" role="img" aria-label="Photo of colleagues reviewing work on a laptop"></div>
  <div class="card" style="left:97px;top:1660px;width:534px;height:268px">
    <div class="kicker">Vellum Layout</div>
    <h3>Many desktop publishing packages web page editors now use Lorem Ipsum</h3>
    <p>It is a long established fact that a reader will be distracted by the readable content of a page when looking at its layout. The point of using Lorem Ipsum is that it has a more-or-less normal distribution of letters, as opposed to using 'Content here, content here', making it look like readable English.</p>
  </div>
</section>

<section class="video-band" role="img" aria-label="Background photo of a business discussion, darkened">
  <svg class="play" width="54" height="54" viewBox="0 0 54 54"><circle cx="27" cy="27" r="25" fill="none" stroke="#fff" stroke-width="2.5"/><polygon points="21,16 38,27 21,38" fill="#fff"/></svg>
  <h2 class="display">CHECK OUR VIDEO</h2>
  <p>There are many variations of passages of Lorem Ipsum available, but the majority</p>
  <div class="btn" style="left:523px;top:268px;width:154px;height:34px;background:var(--sky);color:#fff;font-weight:400">MORE ABOUT US</div>
</section>

<section class="services">
  <h2 class="section-title display" style="top:2475px">WHAT WE DO</h2>
  <div class="service" style="left:64px">
    <div class="ring"><span><svg width="40" height="34" viewBox="0 0 34 30"><polyline points="2,2 2,28 33,28" fill="none" stroke="#333" stroke-width="2"/><polyline points="5,22 13,13 19,18 31,5" fill="none" stroke="#333" stroke-width="2.5"/></svg></span></div>
    <h4>Business Analysis</h4>
    <p>It is a long established fact that reader<br>will be distracted by readable</p>
  </div>
  <div class="service" style="left:327px">
    <div class="ring"><span><svg width="38" height="32" viewBox="0 0 38 32"><rect x="13" y="2" width="12" height="6" fill="none" stroke="#333" stroke-width="2.5"/><rect x="2" y="8" width="34" height="22" rx="2" fill="#333"/><rect x="16" y="16" width="6" height="4" fill="#fff"/></svg></span></div>
    <h4>Best Consultancy</h4>
    <p>It is a long established fact that reader<br>will be distracted by readable</p>
  </div>
  <div class="service" style="left:593px">
    <div class="ring"><span><svg width="40" height="32" viewBox="0 0 40 32"><circle cx="20" cy="8" r="6" fill="#333"/><circle cx="8" cy="12" r="4.5" fill="#333"/><circle cx="32" cy="12" r="4.5" fill="#333"/><path d="M10 30 Q10 16 20 16 Q30 16 30 30Z" fill="#333"/><path d="M0 28 Q0 19 8 19 Q11 19 12 20 Q9 24 9 28Z" fill="#333"/><path d="M40 28 Q40 19 32 19 Q29 19 28 20 Q31 24 31 28Z" fill="#333"/></svg></span></div>
    <h4>Full Time Recruiter</h4>
    <p>It is a long established fact that reader<br>will be distracted by readable</p>
  </div>
  <div class="service" style="left:856px">
    <div class="ring"><span><svg width="22" height="34" viewBox="0 0 22 34"><rect x="2" y="2" width="18" height="30" rx="3" fill="none" stroke="#333" stroke-width="2.5"/><circle cx="11" cy="27" r="1.8" fill="#333"/></svg></span></div>
    <h4>24/7 Online Support</h4>
    <p>It is a long established fact that reader<br>will be distracted by readable</p>
  </div>
  <div class="btn btn-navy" style="left:444px;top:2816px;width:125px;height:38px">READ MORE</div>
  <div class="btn btn-outline" style="left:595px;top:2816px;width:158px;height:38px">GET START NOW</div>
</section>

<section class="news">
  <div class="news-band"></div>
  <div class="callback">
    <h3>REQUEST A CALL BACK</h3>
    <p>Contrary to popular belief, Lorem Ipsum is not simply random text it has roots</p>
    <div class="field">Your Name</div>
    <div class="field">Your phone number</div>
    <div class="field">Your Email</div>
    <div class="submit">SUBMIT NOW</div>
  </div>
  <h2 class="news-title display">LATEST NEWS</h2>
  <article class="news-card" style="left:462px">
    <div class="pic" style="background:linear-gradient(120deg,#3c4550,#8a8f95 60%,#55606b)" role="img" aria-label="Photo of business people shaking hands"></div>
    <h4>Harrowgate College</h4>
    <p>There are many variations of passages of Lorem Ipsum available, but the majority have</p>
    <a>Read More</a>
  </article>
  <article class="news-card" style="left:804px">
    <div class="pic" style="background:linear-gradient(120deg,#6f8fb3,#a9c1da 55%,#5b7ea5)" role="img" aria-label="Illustration of a network of people with one highlighted"></div>
    <h4>Harrowgate College</h4>
    <p>There are many variations of passages of Lorem Ipsum available, but the majority have</p>
    <a>Read More</a>
  </article>
</section>

<footer class="footer">
  <div class="brand" style="top:3460px">marcus fenwold</div>
  <p class="about-text">There are many variations of passages of Lorem Ipsum available, but the majority have suffered alteration in some form, by injected humour, or randomised words There are many variations of passages of Lorem Ipsum</p>
  <div class="socials"><span></span><span></span><span></span><span></span><span></span></div>

  <div class="contact" style="left:458px">
    <span class="dot"><svg width="14" height="18" viewBox="0 0 14 18"><path d="M7 1 Q13 1 13 7 Q13 11 7 17 Q1 11 1 7 Q1 1 7 1Z" fill="#fff"/><circle cx="7" cy="7" r="2.3" fill="#222"/></svg></span>
    <span>1420 Linden Ave, Westbrook,<br>FL 33011</span>
  </div>
  <div class="contact" style="left:720px">
    <span class="dot"><svg width="16" height="16" viewBox="0 0 16 16"><path d="M3 1 L6 1 L7 5 L5 6.5 Q6.5 9.5 9.5 11 L11 9 L15 10 L15 13 Q15 15 13 15 Q1 14 1 3 Q1 1 3 1Z" fill="#fff"/></svg></span>
    <span>555-204-7781</span>
  </div>
  <div class="contact" style="left:898px">
    <span class="dot"><svg width="18" height="13" viewBox="0 0 18 13"><rect x="0" y="0" width="18" height="13" rx="1" fill="#fff"/><polyline points="1,1 9,7 17,1" fill="none" stroke="#222" stroke-width="1.5"/></svg></span>
    <span>info@companyname.com</span>
  </div>
  <div class="rule"></div>

  <div class="col" style="left:475px"><h5>QUICKLINK</h5><ul><li>Home</li><li>About us</li><li>Services</li><li>Blog</li></ul></div>
  <div class="col" style="left:659px"><h5>SERVICES</h5><ul><li>24/7 Support</li><li>Expert review</li><li>Successful Project</li></ul></div>
  <div class="col newsletter" style="left:863px"><h5>NEWSLETTER</h5><p style="font-size:12px;color:#444">Sign up for our newsletter</p><div class="input">Email</div><div class="go">SUBSCRIBE</div></div>

  <div class="copyright">Copyright@2017Company Name , All rights Reserved</div>
</footer>

</body>
</html>
```